Classy, Elegant, Simple Business Card Design

Looking to have a classy, simple, and elegant design. Want a top notch designed business card. I really like the look of the new torvane credit card. I also like the design I attached. I am trying to reach 21-29 year old females for booking us for there wedding or event. We offer Disc Jockey Service, Photo Booth Rentals, and Uplighting .

Target Market(s)

21-28 year old females

Contact Information for Business Card

Has to have logo, website, email, and phone number

Font styles to use
Other font styles liked:
• open to font choice, modern, clean
Designer to choose
33a6d7
0791cd
0555a3
ffffff

Requirements
Must have
• Has to have logo, website, email, and phone number
Nice to have
• I really like the design of the new torvane credit card. I also included my logo and some designs I like
Should not have
• clutter or too much info

```html
<!DOCTYPE html>
<html lang="en">
<head>
<meta charset="utf-8">
<title>Echoline Event Group – Business Card</title>
<link href="https://fonts.googleapis.com/css2?family=Poppins:wght@300;600&family=Roboto:wght@400;700&display=swap" rel="stylesheet">
<style>
  :root{
    --bg:#2c2d30;
    --card-dark:#1d1e21;
    --card-dark-2:#26272b;
    --blue-light:#33a6d7;
    --blue-mid:#0791cd;
    --blue-deep:#0555a3;
    --silver:#b9bcc2;
    --grey-text:#8d9096;
    --white:#ffffff;
  }
  *{margin:0;padding:0;box-sizing:border-box}
  html,body{width:799px;height:1200px;overflow:hidden;background:var(--bg)}
  .canvas{position:relative;width:799px;height:1200px}
  .card{
    position:absolute;left:80px;width:640px;height:366px;
    border-radius:4px;overflow:hidden;
    background:linear-gradient(135deg,var(--card-dark-2),var(--card-dark));
    box-shadow:0 14px 30px rgba(0,0,0,.45);
  }
  .card--front{top:110px}
  .card--back{top:690px}

  /* front */
  .front-brand{
    position:absolute;left:0;right:0;top:110px;text-align:center;
    font-family:"Poppins",sans-serif;
  }
  .brand-mark{
    display:inline-block;width:22px;height:22px;border-radius:50%;
    background:var(--blue-mid);vertical-align:middle;margin-right:12px;
  }
  .brand-name{
    display:inline-block;vertical-align:middle;
    font-weight:600;font-size:40px;letter-spacing:3px;color:var(--blue-mid);
  }
  .brand-tagline{
    margin-top:6px;font-family:"Poppins",sans-serif;font-weight:300;
    font-size:15px;letter-spacing:9px;color:var(--grey-text);
  }
  .equalizer-band{
    position:absolute;left:0;right:0;bottom:0;height:92px;
    background:linear-gradient(to top,var(--blue-deep) 0%,var(--blue-light) 55%,rgba(51,166,215,0) 100%);
    clip-path:polygon(0 45%,20% 30%,40% 55%,60% 25%,80% 40%,100% 20%,100% 100%,0 100%);
    opacity:.9;
  }

  /* back */
  .back-art{position:absolute;inset:0}
  .back-brand{
    position:absolute;left:150px;top:62px;font-family:"Poppins",sans-serif;
  }
  .back-brand .brand-name{color:var(--white);font-size:34px}
  .back-brand .brand-mark{background:var(--white);width:18px;height:18px}
  .back-brand .brand-tagline{color:#d6e6f5;font-size:13px;letter-spacing:8px;margin-left:30px;margin-top:2px}
  .person{
    position:absolute;left:44px;top:238px;font-family:"Roboto",sans-serif;
  }
  .person-name{font-weight:700;font-size:25px;color:var(--blue-mid)}
  .person-role{margin-top:4px;font-size:15px;color:var(--white)}
  .contact-list{
    position:absolute;left:300px;top:236px;list-style:none;
    font-family:"Roboto",sans-serif;font-size:16px;color:var(--white);
  }
  .contact-item{display:flex;align-items:center;gap:12px;height:27px}
  .contact-icon{width:14px;height:14px;flex:none}
</style>
</head>
<body>
<main class="canvas">

  <section class="card card--front" aria-label="Card front">
    <div class="front-brand">
      <span class="brand-mark"></span><span class="brand-name">ECHOLINE</span>
      <p class="brand-tagline">EVENT GROUP</p>
    </div>
    <div class="equalizer-band" role="img" aria-label="Blue sound equalizer bars along the bottom edge"></div>
  </section>

  <section class="card card--back" aria-label="Card back">
    <svg class="back-art" width="640" height="366" viewBox="0 0 640 366">
      <defs>
        <linearGradient id="bandFill" x1="0" y1="0" x2="1" y2="1">
          <stop offset="0" stop-color="#0555a3"/>
          <stop offset="1" stop-color="#0791cd"/>
        </linearGradient>
      </defs>
      <path d="M0 0 H640 V232 Q330 150 0 128 Z" fill="url(#bandFill)"/>
      <path d="M0 136 Q330 158 640 242" fill="none" stroke="#b9bcc2" stroke-width="7"/>
    </svg>

    <div class="back-brand">
      <span class="brand-mark"></span><span class="brand-name">ECHOLINE</span>
      <p class="brand-tagline">EVENT GROUP</p>
    </div>

    <div class="person">
      <p class="person-name">Marcus Hale</p>
      <p class="person-role">Founder &amp; CEO</p>
    </div>

    <ul class="contact-list">
      <li class="contact-item">
        <svg class="contact-icon" viewBox="0 0 16 16"><path d="M3 1h3l1 4-2 1a9 9 0 0 0 5 5l1-2 4 1v3a2 2 0 0 1-2 2A13 13 0 0 1 1 3a2 2 0 0 1 2-2z" fill="#0791cd"/></svg>
        <span>555 0142 0199</span>
      </li>
      <li class="contact-item">
        <svg class="contact-icon" viewBox="0 0 16 16"><rect x="1" y="3" width="14" height="10" rx="1" fill="#0791cd"/><path d="M1 4l7 5 7-5" fill="none" stroke="#1d1e21" stroke-width="1.3"/></svg>
        <span>marcus@echoline.com</span>
      </li>
      <li class="contact-item">
        <svg class="contact-icon" viewBox="0 0 16 16"><circle cx="8" cy="8" r="7" fill="#0791cd"/><path d="M1 8h14M8 1c3 3 3 11 0 14M8 1c-3 3-3 11 0 14" fill="none" stroke="#1d1e21" stroke-width="1.1"/></svg>
        <span>www.echoline.com</span>
      </li>
    </ul>
  </section>

</main>
</body>
</html>
```